Veldmark Supplies Business Card

Professional business card that stand out to our potential customers. Front and back with clean modern design

Industry/Entity Type

Oil and gas

Contact Information for Business Card

Name, address, website , office phone and cell number

Requirements
Must have
• Editable files for each employee

```html
<!DOCTYPE html>
<html lang="en">
<head>
<meta charset="utf-8">
<title>Veldmark Supplies Business Card</title>
<link href="https://fonts.googleapis.com/css2?family=Roboto:wght@400;500;700;900&display=swap" rel="stylesheet">
<style>
  :root {
    --stage: #2b2b2d;
    --red: #e01f26;
    --blue: #24acd1;
    --white: #ffffff;
    --grad-blue: #2fb4d6;
    --grad-red: #e0222b;
  }
  * { margin: 0; padding: 0; box-sizing: border-box; }
  html, body { width: 1200px; height: 852px; overflow: hidden; }
  body {
    background: var(--stage);
    font-family: "Roboto", Arial, sans-serif;
    position: relative;
  }
  .card {
    position: absolute;
    top: 288px;
    width: 480px;
    height: 275px;
    border-radius: 22px;
    overflow: hidden;
  }
  /* Back side */
  .card-back {
    left: 90px;
    background: linear-gradient(45deg, var(--grad-blue) 0%, #8a5872 50%, var(--grad-red) 100%);
    display: flex;
    align-items: center;
    justify-content: center;
  }
  .brand-lockup {
    display: flex;
    align-items: center;
    gap: 10px;
  }
  .brand-mark {
    width: 18px;
    height: 18px;
    background: var(--white);
  }
  .brand-name {
    font-weight: 900;
    font-size: 26px;
    letter-spacing: 1px;
    text-transform: uppercase;
    color: var(--white);
    white-space: nowrap;
  }
  /* Front side */
  .card-front { left: 630px; background: var(--white); }
  .card-front .bands { position: absolute; inset: 0; width: 100%; height: 100%; }
  .front-lockup {
    position: absolute;
    left: 24px;
    top: 60px;
  }
  .front-lockup .brand-mark { background: var(--red); width: 14px; height: 14px; }
  .front-lockup .brand-name { color: var(--red); font-size: 20px; }
  .person {
    position: absolute;
    left: 24px;
    top: 128px;
    color: var(--white);
  }
  .person-name { font-size: 18px; font-weight: 700; }
  .person-title { font-size: 11px; margin-top: 3px; }
  .contact {
    position: absolute;
    left: 24px;
    top: 198px;
    list-style: none;
    color: var(--white);
    font-size: 11.5px;
    line-height: 16px;
  }
  .contact li { display: flex; align-items: center; gap: 7px; white-space: nowrap; }
  .contact svg { width: 10px; height: 10px; flex: none; }
  .contact .address { margin-top: 4px; }
</style>
</head>
<body>

<section class="card card-back" aria-label="Card back">
  <div class="brand-lockup">
    <span class="brand-mark"></span>
    <span class="brand-name">Veldmark Supplies</span>
  </div>
</section>

<section class="card card-front" aria-label="Card front">
  <svg class="bands" viewBox="0 0 480 275" preserveAspectRatio="none" aria-hidden="true">
    <rect x="444" y="0" width="36" height="100" fill="var(--blue)"/>
    <polygon points="0,118 480,98 480,150 0,188" fill="var(--blue)"/>
    <polygon points="0,188 480,150 480,275 0,275" fill="var(--red)"/>
  </svg>

  <div class="front-lockup brand-lockup">
    <span class="brand-mark"></span>
    <span class="brand-name">Veldmark Supplies</span>
  </div>

  <div class="person">
    <div class="person-name">Mara Ellison</div>
    <div class="person-title">Managing Director</div>
  </div>

  <ul class="contact">
    <li>
      <svg viewBox="0 0 10 10"><path d="M2 1l2 2-1 1.2c.6 1.2 1.6 2.2 2.8 2.8L7 6l2 2-1.2 1.2C4.5 9 1 5.5.8 2.2z" fill="currentColor"/></svg>
      (555)014-2290
    </li>
    <li>
      <svg viewBox="0 0 10 10"><rect x="0.5" y="2" width="9" height="6" fill="none" stroke="currentColor"/><path d="M0.5 2l4.5 3.5L9.5 2" fill="none" stroke="currentColor"/></svg>
      sales@veldmarksupplies.com
    </li>
    <li>
      <svg viewBox="0 0 10 10"><circle cx="5" cy="5" r="4.3" fill="none" stroke="currentColor"/><path d="M.7 5h8.6M5 .7c-2 2.5-2 6.1 0 8.6M5 .7c2 2.5 2 6.1 0 8.6" fill="none" stroke="currentColor" stroke-width=".8"/></svg>
      www.veldmarksupplies.com
    </li>
    <li class="address">418 Harlow Ave Suite 3 Midland, Tx 79701</li>
  </ul>
</section>

</body>
</html>
```